Brightfield Ventures Inc. Letterhead

Creation of attractive and eye catching letterhead for a business start-up for the construction industry. Letterhead must relate to construction, but avoid standard hammer and tools in the design.

I forgot to add some details, sorry about that. Some pertinent info: Ph: 916-555-0187 brightfieldventures.example 448 Willowmere Ave, Ste 210 Folsom, CA 95999 info@brightfieldventures.example not sure if slogan should be in there" “Connecting construction professionals to create a purpose driven industry.” must be able to be used in word. Thanks!

```html
<!DOCTYPE html>
<html lang="en">
<head>
<meta charset="utf-8">
<title>Brightfield Ventures Inc. Letterhead</title>
<link rel="stylesheet" href="https://fonts.googleapis.com/css2?family=Arimo:wght@400;700&display=swap">
<style>
  :root {
    --backdrop: #b9cbe6;
    --paper: #ffffff;
    --navy: #1c2a6b;
    --blue: #2f4db3;
    --light-blue: #c9d5f5;
    --red: #d01f26;
    --ink: #1d1d1f;
    --muted: #6f7378;
    --rule: #d4d6da;
  }
  * { box-sizing: border-box; margin: 0; padding: 0; }
  html, body { width: 1200px; height: 784px; overflow: hidden; }
  body {
    background: var(--backdrop);
    font-family: "Arimo", Arial, sans-serif;
    color: var(--ink);
  }
  .letterhead {
    position: absolute;
    left: 338px;
    top: 22px;
    width: 523px;
    height: 740px;
    background: var(--paper);
    box-shadow: 0 6px 18px rgba(30, 50, 90, 0.18);
    overflow: hidden;
  }
  .top-rule {
    position: absolute;
    left: 0; top: 0;
    width: 205px; height: 3px;
    background: var(--red);
  }
  .brand {
    position: absolute;
    left: 38px; top: 36px;
    display: flex;
    align-items: center;
    gap: 8px;
  }
  .brand-mark {
    width: 14px; height: 14px;
    background: var(--red);
  }
  .brand-name {
    font-weight: 700;
    font-size: 17px;
    letter-spacing: 0.5px;
    color: var(--navy);
    text-transform: uppercase;
  }
  .contact {
    position: absolute;
    left: 352px; top: 62px;
    padding-left: 12px;
    border-left: 1px solid var(--rule);
    list-style: none;
    font-size: 6.6px;
    line-height: 1.55;
    color: var(--muted);
  }
  .contact li { display: flex; align-items: flex-start; gap: 5px; }
  .contact-dot {
    flex: none;
    width: 5px; height: 5px;
    margin-top: 2px;
    border-radius: 50%;
    background: var(--red);
  }
  .letter-body {
    position: absolute;
    left: 118px; top: 150px;
    width: 322px;
    font-size: 9.6px;
    line-height: 1.38;
    text-align: left;
  }
  .letter-body p + p { margin-top: 12px; }
  .faint-name {
    position: absolute;
    left: 28px; bottom: 150px;
    font-weight: 700;
    font-size: 30px;
    color: #eceef2;
    text-transform: uppercase;
    letter-spacing: 1px;
  }
  .footer-bands {
    position: absolute;
    left: 0; bottom: 0;
    width: 523px; height: 120px;
  }
</style>
</head>
<body>
  <main class="letterhead">
    <div class="top-rule"></div>

    <header class="brand">
      <span class="brand-mark"></span>
      <span class="brand-name">Brightfield Ventures</span>
    </header>

    <ul class="contact">
      <li><span class="contact-dot"></span><span>448 Willowmere Ave, Ste 210<br>Folsom, CA 95999</span></li>
      <li><span class="contact-dot"></span><span>916-555-0187</span></li>
      <li><span class="contact-dot"></span><span>916-555-0188</span></li>
      <li><span class="contact-dot"></span><span>info@brightfieldventures.example</span></li>
      <li><span class="contact-dot"></span><span>www.brightfieldventures.example</span></li>
    </ul>

    <section class="letter-body">
      <p>Lorem Ipsum is simply dummy text of the printing and typesetting industry. Lorem Ipsum has been the industry's standard dummy text ever since the 1500s, when an unknown printer took a galley of type and scrambled it to make a type specimen book. It has survived not only five centuries, but also the leap into electronic typesetting, remaining essentially unchanged. It was popularised in the 1960s with the release of Typeline sheets containing Lorem Ipsum passages, and more recently with desktop publishing software like Pagecraft Studio including versions of Lorem Ipsum.</p>
      <p>It is a long established fact that a reader will be distracted by the readable content of a page when looking at its layout. The point of using Lorem Ipsum is that it has a more-or-less normal distribution of letters, as opposed to using 'Content here, content here', making it look like readable English. Many desktop publishing packages and web page editors now use Lorem Ipsum as their default model text, and a search for 'lorem ipsum' will uncover many web sites still in their infancy. Various versions have evolved over the years, sometimes by accident, sometimes on purpose (injected humour and the like).</p>
      <p>Contrary to popular belief, Lorem Ipsum is not simply random text. It has roots in a piece of classical Latin literature from 45 BC, making it over 2000 years old. Daniel Ashworth, a Latin professor at Northvale College in Virginia, looked up one of the more obscure Latin words, consectetur, from a Lorem Ipsum passage, and going through the cites of the word in classical literature, discovered the undoubtable source. Lorem Ipsum comes from sections 1.10.32 and 1.10.33 of "de Finibus Bonorum et Malorum" structures, to generate Lorem Ipsum which looks reasonable. The generated Lorem Ipsum is therefore always free from repetition, injected humour, or non-characteristic words etc.</p>
    </section>

    <div class="faint-name">Brightfield</div>

    <svg class="footer-bands" viewBox="0 0 523 120" aria-hidden="true">
      <defs>
        <linearGradient id="fade" x1="0" y1="0" x2="1" y2="0">
          <stop offset="0.18" stop-color="#fff" stop-opacity="0"/>
          <stop offset="0.62" stop-color="#fff" stop-opacity="1"/>
        </linearGradient>
        <mask id="band-fade">
          <rect width="523" height="120" fill="url(#fade)"/>
        </mask>
        <linearGradient id="blue-band" x1="0" y1="0" x2="0" y2="1">
          <stop offset="0" stop-color="var(--light-blue)"/>
          <stop offset="1" stop-color="var(--blue)"/>
        </linearGradient>
      </defs>
      <g mask="url(#band-fade)">
        <polygon points="0,70 523,52 523,80 0,90" fill="url(#blue-band)"/>
        <polygon points="0,90 523,80 523,88 0,95" fill="var(--red)"/>
        <polygon points="0,97 523,92 523,100 0,103" fill="var(--navy)"/>
        <polygon points="0,104 523,102 523,109 0,109" fill="var(--red)"/>
        <polygon points="0,110 523,111 523,120 0,120" fill="var(--navy)"/>
      </g>
      <rect x="0" y="117" width="320" height="3" fill="var(--red)"/>
    </svg>
  </main>
</body>
</html>
```